Business card

I need a business card design for my consulting company in animal welfare for livestock. I like clean, crisp, simple.

One I imagined was double-sided:
side1: just my name and contact information
side2: silhouette of farm animals. Could be 3 (pig, cow, chicken) or all the species (pig, cow, chicken, duck, sheep, rabbit, etc) that continue the length of the card. I have attached an image of a silhouette style.

But, I am open to any concept.

```html
<!DOCTYPE html>
<html lang="en">
<head>
<meta charset="utf-8">
<title>Business Card – Helen Marwick</title>
<link rel="stylesheet" href="https://fonts.googleapis.com/css2?family=Arimo:wght@400&display=swap">
<style>
  :root {
    --paper: #ffffff;
    --ink: #000000;
  }

  html, body {
    margin: 0;
    padding: 0;
    width: 1200px;
    height: 741px;
    overflow: hidden;
    background: var(--paper);
  }

  .business-card {
    position: relative;
    width: 1200px;
    height: 741px;
    background: var(--paper);
    font-family: "Arimo", Arial, Helvetica, sans-serif;
    color: var(--ink);
  }

  .card-frame {
    position: absolute;
    left: 49px;
    top: 48px;
    width: 1101px;
    height: 642px;
    box-sizing: border-box;
    border: 6px solid var(--ink);
  }

  .card-text {
    position: absolute;
    left: 0;
    right: 0;
    top: 224px;
    margin: 0;
    text-align: center;
    font-size: 51px;
    line-height: 63px;
    font-weight: 400;
    white-space: nowrap;
  }

  .card-text p {
    margin: 0;
  }

  .identity {
    margin-bottom: 67px;
  }
</style>
</head>
<body>
  <main class="business-card">
    <div class="card-frame"></div>

    <div class="card-text">
      <div class="identity">
        <p class="person-name">Helen Marwick</p>
        <p class="service-line">Humane Care Consulting for Farm Operations</p>
      </div>
      <div class="contact">
        <p class="contact-email">Email: helen.marwick@mailbox.com</p>
        <p class="contact-phone">Tel: +1.604.555.0182</p>
      </div>
    </div>
  </main>
</body>
</html>
```